Stationary design for boutique production house

We need a stationary design for our production house, 'Lorno Productions' based in Singapore. We produce microfilms as well as podcasts, talkshows and events. Our logo is a stylized icon of our director, who is also the executive producer and host of our programs, Lorno. Our main company colors are Red, Black and white. We would like a clean, minimalist design incorporating our existing company logo that conveys a sense of urbanism and elegance.

Logo and font files are attached. f

Target Market(s)

We focus on lifestyle media rather than entertainment.

Industry/Entity Type

Boutique

Font styles to use
Serif
Sans Serif

Colors
ec1f27
ffffff
000000

Requirements
Must have
• Our company logo and at least one of our company colors.
Nice to have
• Our address and contact information.
Should not have
• Changes made to the company logo (using only certain parts of it is fine though)

```html
<!DOCTYPE html>
<html lang="en">
<head>
<meta charset="utf-8">
<title>Lorno Productions — Business Cards</title>
<link rel="stylesheet" href="https://fonts.googleapis.com/css2?family=Bodoni+Moda:wght@500&family=Jost:wght@400;500&display=swap">
<style>
  :root {
    --red: #ec1f27;
    --black: #231f20;
    --white: #ffffff;
    --grey-text: #4a4a4a;
    --backdrop: #3b3b3b;
    --rule: #9a9a9a;
    --mark-light: #f4f4f4;
  }
  * { box-sizing: border-box; margin: 0; padding: 0; }
  html, body {
    width: 1200px; height: 659px; overflow: hidden;
    background: var(--backdrop);
  }
  .stage {
    width: 1200px; height: 659px;
    display: flex; align-items: center; justify-content: center; gap: 80px;
  }
  .card {
    width: 320px; height: 540px;
    position: relative; overflow: hidden;
    box-shadow: 0 10px 28px rgba(0,0,0,.45);
  }
  .card--front { background: var(--white); color: var(--black); }
  .card--back  { background: var(--black); color: var(--white); }

  .logo-area { position: absolute; }
  .card--front .logo-area {
    top: 58px; left: 95px; width: 130px; height: 96px;
    background: var(--black); border-radius: 65px 65px 0 0;
  }
  .card--back .logo-area {
    top: 300px; left: 20px; width: 300px; height: 240px;
    background: var(--mark-light); border-radius: 150px 0 0 0;
  }

  .wordmark {
    display: flex; align-items: center; justify-content: center; gap: 10px;
    font-family: "Bodoni Moda", serif; font-weight: 500;
    font-size: 22px; letter-spacing: .02em; text-transform: uppercase;
    line-height: 1.05; text-align: center;
  }
  .wordmark__dot {
    width: 10px; height: 10px; border-radius: 50%;
    background: var(--red); flex: none;
  }
  .card--front .wordmark { position: absolute; top: 166px; left: 0; right: 0; color: var(--black); }
  .divider {
    position: absolute; top: 224px; left: 55px; right: 55px;
    border-top: 1px solid var(--rule);
  }

  .person {
    position: absolute; top: 248px; left: 0; right: 0; text-align: center;
    font-family: "Jost", sans-serif;
  }
  .person__name { font-size: 19px; letter-spacing: .04em; text-transform: uppercase; color: var(--black); font-weight: 400; }
  .person__role { font-size: 14px; letter-spacing: .03em; text-transform: uppercase; color: var(--red); margin-top: 2px; }

  .address {
    position: absolute; top: 318px; left: 0; right: 0; text-align: center;
    font-family: "Jost", sans-serif; font-size: 13px; line-height: 1.45;
    color: var(--grey-text); letter-spacing: .04em; font-style: normal;
  }
  .contacts {
    position: absolute; top: 370px; left: 82px;
    list-style: none;
    font-family: "Jost", sans-serif; font-size: 13px; line-height: 1.55;
    color: var(--grey-text); letter-spacing: .05em;
  }
  .contacts li { display: flex; align-items: center; gap: 9px; }
  .contacts svg { width: 12px; height: 12px; fill: var(--black); flex: none; }

  .card--back .wordmark { position: absolute; top: 92px; left: 0; right: 0; color: var(--white); font-size: 24px; }
  .card--back .web {
    position: absolute; top: 160px; left: 0; right: 0; text-align: center;
    font-family: "Jost", sans-serif; font-size: 12px; letter-spacing: .16em; color: var(--white);
  }
</style>
</head>
<body>
<main class="stage">
  <section class="card card--front" aria-label="Business card front">
    <div class="logo-area" role="img" aria-label="Company logo symbol"></div>
    <div class="wordmark"><span>Lorno<br>Productions</span><span class="wordmark__dot"></span></div>
    <div class="divider"></div>
    <div class="person">
      <p class="person__name">Mara Lin</p>
      <p class="person__role">CEO/Founder</p>
    </div>
    <address class="address">42 Keong Saik Road<br>Singapore 089154</address>
    <ul class="contacts">
      <li><svg viewBox="0 0 12 12" aria-hidden="true"><path d="M2.5 1l2 2.3-1 1.3a7 7 0 0 0 3.9 3.9l1.3-1 2.3 2-1.2 1.5C5.5 11 1 6.5 1 2.2z"/></svg>+65 6512 3840</li>
      <li><svg viewBox="0 0 12 12" aria-hidden="true"><rect x="3" y="1" width="6" height="3"/><rect x="1" y="4.5" width="10" height="4.5" rx="1"/><rect x="3" y="8" width="6" height="3"/></svg>+65 6512 3841</li>
      <li><svg viewBox="0 0 12 12" aria-hidden="true"><rect x="3.5" y="1" width="5" height="10" rx="1"/></svg>+65 9187 2261</li>
      <li><svg viewBox="0 0 12 12" aria-hidden="true"><path d="M1 2.5h10v7H1z M1 2.5l5 4 5-4" stroke="#fff" stroke-width=".8"/></svg>mara@lornoprod.com</li>
      <li><svg viewBox="0 0 12 12" aria-hidden="true"><circle cx="6" cy="6" r="5"/><path d="M1 6h10M6 1c-2 2.5-2 7.5 0 10M6 1c2 2.5 2 7.5 0 10" stroke="#fff" stroke-width=".7" fill="none"/></svg>www.lornoprod.com</li>
    </ul>
  </section>

  <section class="card card--back" aria-label="Business card back">
    <div class="wordmark"><span>Lorno<br>Productions</span><span class="wordmark__dot"></span></div>
    <p class="web">www.lornoprod.com</p>
    <div class="logo-area" role="img" aria-label="Large cropped company logo symbol"></div>
  </section>
</main>
</body>
</html>
```